Roofing Contractor business card redesign

I want to redesign my business card with a fresh, eye catching concept

Target Market(s)

Residential Roofing Clients, potential employees, and subcontractors.

Industry/Entity Type

Business

Colors

Designer to choose colors to be used in the design.

Requirements
Nice to have
• I just want something that's more pleasing to the eye. You can use a combination of either / or of my logos.

```html
<!DOCTYPE html>
<html lang="en">
<head>
<meta charset="utf-8">
<title>Fair Deal General Contractors – Business Card</title>
<link href="https://fonts.googleapis.com/css2?family=Roboto:wght@400;500&family=Roboto+Condensed:wght@700&display=swap" rel="stylesheet">
<style>
  :root {
    --backdrop: #e9e4df;
    --brown: #3b1f20;
    --brown-text: #4a1d1a;
    --orange: #e8731f;
    --card-white: #f3f3f3;
    --grey-text: #555555;
    --rule: #8a8a8a;
    --white: #ffffff;
  }
  * { margin: 0; padding: 0; box-sizing: border-box; }
  html, body {
    width: 1200px; height: 960px; overflow: hidden;
    background: var(--backdrop);
    font-family: "Roboto", Arial, sans-serif;
  }
  .canvas { position: relative; width: 1200px; height: 960px; }

  .card { position: absolute; border-radius: 18px; box-shadow: 0 4px 10px rgba(0,0,0,.25); }

  .card-front {
    left: 320px; top: 108px; width: 602px; height: 344px;
    background: var(--brown);
  }
  .front-emblem {
    position: absolute; left: 213px; top: 59px; width: 190px; height: 190px;
    border-radius: 50%; border: 4px solid var(--white);
    background: radial-gradient(circle at 50% 45%, #f0a040 0%, #d9731f 40%, #e8c45a 70%, #f5f0e6 100%);
  }
  .front-url {
    position: absolute; left: 0; right: 0; top: 279px;
    text-align: center; color: var(--white);
    font-size: 15px; letter-spacing: 5px;
  }

  .card-back {
    left: 320px; top: 493px; width: 600px; height: 342px;
    background: var(--card-white);
    overflow: hidden;
  }
  .name-tab {
    position: absolute; left: -14px; top: 48px; width: 28px; height: 28px;
    border-radius: 50%; background: var(--brown);
  }
  .person-name {
    position: absolute; left: 30px; top: 49px;
    font-family: "Roboto Condensed", "Arial Narrow", sans-serif; font-weight: 700;
    font-size: 21px; color: var(--brown-text);
  }
  .person-titles {
    position: absolute; left: 30px; top: 77px;
    font-size: 15.5px; line-height: 19px; color: var(--orange);
  }
  .company-name {
    position: absolute; right: 30px; top: 32px;
    display: flex; align-items: center; gap: 10px;
    font-family: "Roboto Condensed", "Arial Narrow", sans-serif; font-weight: 700;
    color: var(--brown-text); text-align: right;
  }
  .company-dot { width: 44px; height: 44px; border-radius: 50%; background: var(--brown-text); flex: none; }
  .company-name .main { font-size: 34px; line-height: 36px; display: block; }
  .company-name .sub { font-size: 17px; line-height: 22px; display: block; }
  .divider {
    position: absolute; left: 30px; right: 30px; top: 126px;
    border-top: 1px solid var(--rule);
  }
  .contact-list {
    position: absolute; left: 30px; top: 257px;
    list-style: none; font-size: 14.5px; line-height: 19px; color: var(--grey-text);
  }
  .contact-list li { display: flex; align-items: center; gap: 8px; }
  .contact-list svg { width: 13px; height: 13px; fill: var(--brown-text); flex: none; }
  .office {
    position: absolute; right: 28px; top: 257px;
    text-align: right; font-size: 14.5px; line-height: 19px; color: var(--grey-text);
  }
  .office .web { letter-spacing: 1px; }
</style>
</head>
<body>
<div class="canvas">

  <section class="card card-front">
    <div class="front-emblem" role="img" aria-label="Company emblem illustration of three roofing workers in a circle"></div>
    <p class="front-url">www.fairdealtx.com</p>
  </section>

  <section class="card card-back">
    <span class="name-tab"></span>
    <h1 class="person-name">SAM HOLLOWAY</h1>
    <p class="person-titles">Keller Certified Roof Inspector<br>Licensed Property Adjuster</p>

    <div class="company-name">
      <span class="company-dot"></span>
      <span><span class="main">Fair Deal</span><span class="sub">General Contractors, Inc.</span></span>
    </div>

    <div class="divider"></div>

    <ul class="contact-list">
      <li><svg viewBox="0 0 24 24"><path d="M6.6 10.8a15.1 15.1 0 0 0 6.6 6.6l2.2-2.2a1 1 0 0 1 1-.25 11.4 11.4 0 0 0 3.6.57 1 1 0 0 1 1 1V20a1 1 0 0 1-1 1A17 17 0 0 1 3 4a1 1 0 0 1 1-1h3.5a1 1 0 0 1 1 1c0 1.25.2 2.45.57 3.57a1 1 0 0 1-.25 1z"/></svg>(555) 310-4800</li>
      <li><svg viewBox="0 0 24 24"><path d="M7 1h10a2 2 0 0 1 2 2v18a2 2 0 0 1-2 2H7a2 2 0 0 1-2-2V3a2 2 0 0 1 2-2zm0 3v14h10V4zm5 15.5a1 1 0 1 0 0 2 1 1 0 0 0 0-2z"/></svg>(555) 246-7190</li>
      <li><svg viewBox="0 0 24 24"><path d="M2 5h20v14H2zm2 2v.5l8 5 8-5V7zm0 2.8V17h16V9.8l-8 5z"/></svg>sam@fairdealtx.com</li>
    </ul>

    <address class="office" style="font-style:normal">
      4410 Cedar Ridge Road Suite 108<br>
      Fairview, TX 75069<br>
      <span class="web">www.fairdealtx.com</span>
    </address>
  </section>

</div>
</body>
</html>
```